"Beyond The Grey Harbor" Fictional Book Cover

BEYOND THE GREY HARBOR
By: Derek Falloway

Here's the intro .

"It had been nearly forty years since Tim Ashworth last went to the island from where he was raised. Three months earlier he never would have thought about ever coming back. But life is weird. Things happen quickly and plans change, especially when your very life is at stake. The reason he was going back wasn’t to see old friends...no, no, no. They’re all dead. Of all the kids he grew up with on the island who moved off, he’s the only one still alive. Why?"

Pretty much all just a Lumora book, by the way.

Target Market(s)

fiction readers

Requirements
Must have
• Somewhat of a dark, mysterious cover is what I'd like to see. Use your imagination. I've never written a fiction book before so I'm very open to ideas

Needs to have my name, DEREK FALLOWAY at the bottom. like my other books, all of which are non-fiction
Nice to have
• Mysterious is what I'm looking for. NOT A HORROR story though. More a guy who left the island years ago, but is being called back to escape the rat race of modern, consumerist culture.

Please remember this NEEDS to jump out as a thumbnail on Brevix as people are browsing. Mainly the WORDS need to stick out. Lighter words on a say a blue background.

If you want to try to use the attached pic, or something like this, to reflect an island in the cover, that'd be good.

I've also uploaded a couple images I purchased from Pictoravault, hopefully you can make something work with these.

```html
<!DOCTYPE html>
<html lang="en">
<head>
<meta charset="utf-8">
<title>Beyond The Grey Harbor – Book Cover</title>
<link rel="stylesheet" href="https://fonts.googleapis.com/css2?family=Playfair+Display:wght@400;700;900&display=swap">
<style>
  :root {
    --page-bg: #ffffff;
    --sky-top: #54509c;
    --sky-mid: #6a58a2;
    --sky-glow: #b98fa8;
    --horizon: #ecc9a6;
    --shore: #4a4f5e;
    --water-top: #3f3f86;
    --water-deep: #34357a;
    --title-ink: #ffffff;
    --title-shadow: rgba(20, 14, 50, 0.75);
  }
  * { box-sizing: border-box; margin: 0; padding: 0; }
  html, body {
    width: 720px;
    height: 1200px;
    overflow: hidden;
    background: var(--page-bg);
  }
  .stage {
    position: relative;
    width: 720px;
    height: 1200px;
  }
  .book-cover {
    position: absolute;
    left: 40px;
    top: 126px;
    width: 640px;
    height: 947px;
    overflow: hidden;
    box-shadow: 4px 6px 14px rgba(0, 0, 0, 0.28);
  }
  .cover-photo {
    position: absolute;
    inset: 0;
    background: linear-gradient(
      to bottom,
      var(--sky-top) 0%,
      var(--sky-mid) 35%,
      var(--sky-glow) 50%,
      var(--horizon) 58%,
      var(--shore) 64%,
      var(--shore) 72%,
      var(--water-top) 76%,
      var(--water-deep) 100%
    );
  }
  .cover-title {
    position: absolute;
    left: 0;
    right: 0;
    top: 88px;
    text-align: center;
    color: var(--title-ink);
    font-family: "Playfair Display", serif;
    text-shadow: 2px 3px 3px var(--title-shadow);
  }
  .title-main {
    display: block;
    height: 150px;
    font-size: 172px;
    line-height: 150px;
    font-weight: 400;
    white-space: nowrap;
    transform: scaleX(0.42);
    transform-origin: center;
    letter-spacing: -2px;
  }
  .title-sub {
    display: block;
    margin-top: 6px;
    font-size: 60px;
    line-height: 1;
    font-weight: 700;
    letter-spacing: 1px;
    white-space: nowrap;
  }
  .cover-author {
    position: absolute;
    left: 0;
    right: 0;
    bottom: 68px;
    text-align: center;
    color: var(--title-ink);
    font-family: "Playfair Display", serif;
    font-weight: 700;
    font-size: 44px;
    letter-spacing: 1px;
    text-shadow: 2px 3px 3px var(--title-shadow);
    white-space: nowrap;
  }
</style>
</head>
<body>
  <main class="stage">
    <section class="book-cover">
      <div class="cover-photo" role="img" aria-label="Photograph of an island ferry pier under a purple dusk sky with a warm glow on the horizon, calm water in the foreground"></div>
      <h1 class="cover-title">
        <span class="title-main">BEYOND THE</span>
        <span class="title-sub">GREY HARBOR</span>
      </h1>
      <p class="cover-author">DEREK FALLOWAY</p>
    </section>
  </main>
</body>
</html>
```